Very new and innovative Web design for Property managers of Vacation rentals

We are looking for a new website design for travel agencies and property managers specialised on vacation rentals business, holiday villas and apartments.

The end users of this website are travellers who are looking for a vacation home for their next holiday: this is the reason why the website must be easy to use, attractive, professional, possibly elegant and focused on get new reservations.

This is a draft of our current website: https://intro3.kelumsito.com/
Please consider that we would like to have proposals with a totally different and innovative layout, surprise us!

These are the pages of the website:
• Homepage: feel free to redesign all the homepage as you wish, surprise us with something very new! Please consider that Property manager/Travel agencies usually want to have the opportunity to put in evidence groups of houses with specific characteristics (eg. villas with private swimming pool, apartment in big/small towns, villas with air co, etc…), destinations and tourist areas, and sometimes experiences or activities (please consider that the website layout must be suitable even if some of the previous sections are not used).
• Search page: we’d like to organise the results of the search page in three different ways:
o Grid
o Map
o List
• Property page: to illustrate the characteristics, descriptions, images, …. of the property. It is very important to put in evidence images of the property and to maintain the booking form (and the other call to action bottom – eg. whatsapp) always visible
• Custom pages: static pages composed usually by text, images and call to actions
• Contact us (general form)
• Info request (specific of a property form)
• Booking process
• Blog, organised in four pages:
o Home Page – introduction to the blog
o List of articles
o Single article
o Site Map (presentation of categories and sub-categories)

If possible, we’d prefer to receive the material in Adobe XD or similar so that we can obtain the three versions:
- smartphone
- tablet
- desktop

The website will be then developed in Bootstrap: as a result we’ll need the icons in SVG format (or the library used)

In attachment you can find the map of the website pages

```html
<!DOCTYPE html>
<html lang="en">
<head>
<meta charset="utf-8">
<title>HavenStays – Search Results, Desktop and Mobile</title>
<link href="https://fonts.googleapis.com/css2?family=Playfair+Display:wght@700&family=Open+Sans:wght@400;600;700&display=swap" rel="stylesheet">
<style>
:root{
  --board:#587c6e;
  --green:#1fb487;
  --green-dark:#168a68;
  --ink:#2d3436;
  --muted:#8a949a;
  --line:#e3e7e9;
  --paper:#ffffff;
  --soft:#f4f6f7;
  --footer:#1d2124;
  --footer-text:#aab2b7;
  --photo-a:#5d8a4e;
  --photo-b:#3d8fb8;
  --photo-c:#b88a5a;
}
*{box-sizing:border-box;margin:0;padding:0}
html,body{width:796px;height:1200px;overflow:hidden}
body{background:var(--board);font-family:'Open Sans',Arial,sans-serif;color:var(--ink);position:relative}
.screen{position:absolute;background:var(--paper);box-shadow:0 6px 18px rgba(0,0,0,.25);overflow:hidden}
.label{position:absolute;font-family:'Playfair Display',Georgia,serif;color:#fff;font-size:34px;font-weight:700;white-space:nowrap}
.label--desktop{left:-48px;top:640px;transform:rotate(-90deg);transform-origin:left top;left:26px;top:840px}
.label--mobile{left:770px;top:130px;transform:rotate(90deg);transform-origin:left top}

/* desktop */
.desktop{left:74px;top:120px;width:590px;height:940px}
.topbar{height:42px;display:flex;align-items:center;padding:0 22px;border-bottom:1px solid var(--line)}
.brand{display:flex;align-items:center;gap:5px;font-weight:700;font-size:12px;color:var(--ink)}
.brand__dot{width:12px;height:12px;border-radius:50%;background:var(--green)}
.nav{margin-left:auto;display:flex;gap:16px;font-size:7px;color:var(--muted)}
.btn{background:var(--green);color:#fff;font-weight:600;border-radius:2px;display:inline-flex;align-items:center;justify-content:center}
.nav-btn{margin-left:16px;font-size:7px;padding:5px 12px}
.searchbar{display:flex;align-items:center;gap:8px;padding:10px 22px;background:var(--soft);border-bottom:1px solid var(--line)}
.field{flex:1;height:18px;background:#fff;border:1px solid var(--line);font-size:6px;color:var(--muted);display:flex;align-items:center;padding:0 6px}
.search-btn{font-size:7px;width:64px;height:18px}
.body{display:flex;padding:14px 22px;gap:16px}
.filters{width:110px;font-size:6px;color:var(--muted)}
.filters h4{font-size:7px;color:var(--ink);margin:10px 0 5px}
.filters li{list-style:none;display:flex;align-items:center;gap:4px;margin-bottom:5px}
.check{width:6px;height:6px;border:1px solid #c7cdd1}
.results{flex:1}
.results__head{display:flex;justify-content:space-between;align-items:center;font-size:7px;color:var(--muted);margin-bottom:10px}
.views{display:flex;gap:3px}
.views span{padding:3px 7px;border:1px solid var(--line);font-size:6px}
.views .on{background:var(--green);color:#fff;border-color:var(--green)}
.grid{display:grid;grid-template-columns:repeat(3,1fr);gap:12px}
.card{border:1px solid var(--line)}
.card__photo{height:66px}
.card__info{padding:5px 6px 6px}
.card__title{font-size:7px;font-weight:700}
.card__meta{font-size:5.5px;color:var(--muted);margin:2px 0 5px}
.card__row{display:flex;justify-content:space-between;align-items:center}
.price{font-size:7px;font-weight:700;color:var(--green-dark)}
.card-btn{font-size:6px;width:38px;height:13px}
.pager{display:flex;justify-content:center;gap:4px;margin-top:14px}
.pager span{width:13px;height:13px;border:1px solid var(--line);font-size:6px;display:flex;align-items:center;justify-content:center}
.pager .on{background:var(--green);color:#fff;border-color:var(--green)}
.footer{position:absolute;left:0;right:0;bottom:0;background:var(--footer);color:var(--footer-text);padding:22px 22px 12px;font-size:6px}
.footer__cols{display:flex;gap:40px}
.footer h5{color:#fff;font-size:7px;margin-bottom:6px}
.footer p{margin-bottom:4px}
.footer .brand{color:#fff;font-size:10px}
.footer__copy{border-top:1px solid #33393d;margin-top:16px;padding-top:8px;text-align:center}
.social{display:flex;gap:4px;margin-top:4px}
.social span{width:10px;height:10px;border-radius:50%;background:#3a4145}

/* mobile */
.mobile{left:686px;top:120px;width:100px;height:1060px}
.m-top{height:24px;display:flex;align-items:center;padding:0 6px;border-bottom:1px solid var(--line)}
.m-top .brand{font-size:7px;gap:3px}
.m-top .brand__dot{width:7px;height:7px}
.burger{margin-left:auto;width:9px;height:6px;border-top:1.5px solid var(--ink);border-bottom:1.5px solid var(--ink);position:relative}
.m-search{background:var(--green);padding:6px}
.m-search .field{height:11px;font-size:4.5px}
.m-list{padding:6px}
.m-card{border:1px solid var(--line);margin-bottom:7px}
.m-card .card__photo{height:54px}
.m-card .card__title{font-size:5.5px}
.m-card .card__meta{font-size:4.5px}
.m-card .price{font-size:5.5px}
.m-card .card-btn{font-size:4.5px;width:28px;height:10px}
.m-footer{position:absolute;left:0;right:0;bottom:0;background:var(--footer);color:var(--footer-text);padding:10px 7px;font-size:4.5px}
.m-footer h5{color:#fff;font-size:5.5px;margin:6px 0 3px}
.m-footer p{margin-bottom:2px}
.m-footer .brand{color:#fff;font-size:7px;margin-top:8px}
.m-footer .social span{width:7px;height:7px}

.ph-a{background:linear-gradient(160deg,#8fb86e,var(--photo-a))}
.ph-b{background:linear-gradient(160deg,#7cc4e0,var(--photo-b))}
.ph-c{background:linear-gradient(160deg,#dcb98a,var(--photo-c))}
</style>
</head>
<body>

<div class="label label--desktop">Desktop Version</div>
<div class="label label--mobile">Mobile Version</div>

<section class="screen desktop">
  <header class="topbar">
    <div class="brand"><span class="brand__dot"></span>HavenStays</div>
    <nav class="nav"><span>Home</span><span>Villas</span><span>Destinations</span><span>Blog</span><span>Contact</span></nav>
    <span class="btn nav-btn">Book now</span>
  </header>
  <div class="searchbar">
    <div class="field">Where are you going?</div>
    <div class="field">Check in</div>
    <div class="field">Check out</div>
    <div class="field">Guests</div>
    <span class="btn search-btn">Search</span>
  </div>
  <div class="body">
    <aside class="filters">
      <h4>Property type</h4>
      <ul><li><span class="check"></span>Villa</li><li><span class="check"></span>Apartment</li><li><span class="check"></span>Farmhouse</li><li><span class="check"></span>Cottage</li></ul>
      <h4>Bedrooms</h4>
      <ul><li><span class="check"></span>1 – 2</li><li><span class="check"></span>3 – 4</li><li><span class="check"></span>5 or more</li></ul>
      <h4>Amenities</h4>
      <ul><li><span class="check"></span>Private pool</li><li><span class="check"></span>Air conditioning</li><li><span class="check"></span>Sea view</li><li><span class="check"></span>Pets allowed</li><li><span class="check"></span>Wi‑Fi</li><li><span class="check"></span>Parking</li></ul>
      <h4>Location</h4>
      <ul><li><span class="check"></span>Countryside</li><li><span class="check"></span>Seaside</li><li><span class="check"></span>Town centre</li></ul>
    </aside>
    <main class="results">
      <div class="results__head"><span>42 properties found</span>
        <div class="views"><span class="on">Grid</span><span>Map</span><span>List</span></div></div>
      <div class="grid">
        <article class="card"><div class="card__photo ph-a" role="img" aria-label="Photo of a stone villa with garden"></div><div class="card__info"><div class="card__title">Villa Oliva</div><div class="card__meta">8 guests · 4 bedrooms</div><div class="card__row"><span class="price">€1,250</span><span class="btn card-btn">Details</span></div></div></article>
        <article class="card"><div class="card__photo ph-b" role="img" aria-label="Photo of a villa with swimming pool"></div><div class="card__info"><div class="card__title">Villa Azzurra</div><div class="card__meta">6 guests · 3 bedrooms</div><div class="card__row"><span class="price">€980</span><span class="btn card-btn">Details</span></div></div></article>
        <article class="card"><div class="card__photo ph-c" role="img" aria-label="Photo of a farmhouse terrace"></div><div class="card__info"><div class="card__title">Casale Rosa</div><div class="card__meta">10 guests · 5 bedrooms</div><div class="card__row"><span class="price">€1,640</span><span class="btn card-btn">Details</span></div></div></article>
        <article class="card"><div class="card__photo ph-b" role="img" aria-label="Photo of a pool by the house"></div><div class="card__info"><div class="card__title">Villa Mare</div><div class="card__meta">4 guests · 2 bedrooms</div><div class="card__row"><span class="price">€720</span><span class="btn card-btn">Details</span></div></div></article>
        <article class="card"><div class="card__photo ph-a" role="img" aria-label="Photo of a country cottage"></div><div class="card__info"><div class="card__title">Il Poggio</div><div class="card__meta">6 guests · 3 bedrooms</div><div class="card__row"><span class="price">€860</span><span class="btn card-btn">Details</span></div></div></article>
        <article class="card"><div class="card__photo ph-b" role="img" aria-label="Photo of a villa pool at sunset"></div><div class="card__info"><div class="card__title">Villa Sole</div><div class="card__meta">8 guests · 4 bedrooms</div><div class="card__row"><span class="price">€1,120</span><span class="btn card-btn">Details</span></div></div></article>
        <article class="card"><div class="card__photo ph-c" role="img" aria-label="Photo of a stone house"></div><div class="card__info"><div class="card__title">La Torre</div><div class="card__meta">5 guests · 2 bedrooms</div><div class="card__row"><span class="price">€690</span><span class="btn card-btn">Details</span></div></div></article>
        <article class="card"><div class="card__photo ph-a" role="img" aria-label="Photo of a garden villa"></div><div class="card__info"><div class="card__title">Villa Verde</div><div class="card__meta">7 guests · 3 bedrooms</div><div class="card__row"><span class="price">€940</span><span class="btn card-btn">Details</span></div></div></article>
        <article class="card"><div class="card__photo ph-b" role="img" aria-label="Photo of an apartment with pool"></div><div class="card__info"><div class="card__title">Casa Luna</div><div class="card__meta">4 guests · 2 bedrooms</div><div class="card__row"><span class="price">€610</span><span class="btn card-btn">Details</span></div></div></article>
      </div>
      <div class="pager"><span class="on">1</span><span>2</span><span>3</span><span>›</span></div>
    </main>
  </div>
  <footer class="footer">
    <div class="footer__cols">
      <div><div class="brand"><span class="brand__dot"></span>HavenStays</div></div>
      <div><h5>About us</h5><p>Our story</p><p>Owners</p><p>Careers</p></div>
      <div><h5>Holidays</h5><p>Villas with pool</p><p>Apartments</p><p>Destinations</p></div>
      <div><h5>Help</h5><p>Contact us</p><p>Booking terms</p><p>Privacy</p></div>
      <div><h5>Follow us</h5><div class="social"><span></span><span></span><span></span></div></div>
    </div>
    <div class="footer__copy">© HavenStays – All rights reserved</div>
  </footer>
</section>

<section class="screen mobile">
  <header class="m-top"><div class="brand"><span class="brand__dot"></span>HavenStays</div><span class="burger"></span></header>
  <div class="m-search"><div class="field">Where are you going?</div></div>
  <div class="m-list">
    <article class="m-card"><div class="card__photo ph-b" role="img" aria-label="Photo of a villa with pool"></div><div class="card__info"><div class="card__title">Villa Azzurra</div><div class="card__meta">6 guests · 3 bedrooms</div><div class="card__row"><span class="price">€980</span><span class="btn card-btn">Details</span></div></div></article>
    <article class="m-card"><div class="card__photo ph-a" role="img" aria-label="Photo of a stone villa"></div><div class="card__info"><div class="card__title">Villa Oliva</div><div class="card__meta">8 guests · 4 bedrooms</div><div class="card__row"><span class="price">€1,250</span><span class="btn card-btn">Details</span></div></div></article>
    <article class="m-card"><div class="card__photo ph-c" role="img" aria-label="Photo of a farmhouse"></div><div class="card__info"><div class="card__title">Casale Rosa</div><div class="card__meta">10 guests · 5 bedrooms</div><div class="card__row"><span class="price">€1,640</span><span class="btn card-btn">Details</span></div></div></article>
    <article class="m-card"><div class="card__photo ph-b" role="img" aria-label="Photo of a pool"></div><div class="card__info"><div class="card__title">Villa Mare</div><div class="card__meta">4 guests · 2 bedrooms</div><div class="card__row"><span class="price">€720</span><span class="btn card-btn">Details</span></div></div></article>
    <article class="m-card"><div class="card__photo ph-a" role="img" aria-label="Photo of a cottage"></div><div class="card__info"><div class="card__title">Il Poggio</div><div class="card__meta">6 guests · 3 bedrooms</div><div class="card__row"><span class="price">€860</span><span class="btn card-btn">Details</span></div></div></article>
    <article class="m-card"><div class="card__photo ph-b" role="img" aria-label="Photo of a villa at sunset"></div><div class="card__info"><div class="card__title">Villa Sole</div><div class="card__meta">8 guests · 4 bedrooms</div><div class="card__row"><span class="price">€1,120</span><span class="btn card-btn">Details</span></div></div></article>
    <article class="m-card"><div class="card__photo ph-c" role="img" aria-label="Photo of a stone house"></div><div class="card__info"><div class="card__title">La Torre</div><div class="card__meta">5 guests · 2 bedrooms</div><div class="card__row"><span class="price">€690</span><span class="btn card-btn">Details</span></div></div></article>
    <article class="m-card"><div class="card__photo ph-a" role="img" aria-label="Photo of a garden villa"></div><div class="card__info"><div class="card__title">Villa Verde</div><div class="card__meta">7 guests · 3 bedrooms</div><div class="card__row"><span class="price">€940</span><span class="btn card-btn">Details</span></div></div></article>
  </div>
  <footer class="m-footer">
    <h5>About us</h5><p>Our story</p><p>Owners</p>
    <h5>Holidays</h5><p>Villas with pool</p><p>Apartments</p>
    <h5>Help</h5><p>Contact us</p><p>Privacy</p>
    <h5>Follow us</h5><div class="social"><span></span><span></span><span></span></div>
    <div class="brand"><span class="brand__dot"></span>HavenStays</div>
  </footer>
</section>

</body>
</html>
```